Moravel Aesthetic Doctor

I require an elegant, luxurious looking business card for my aesthetic business. I am a doctor and that will set me aside from competitors. I am planning to provide home and spa based treatments to clients with high expectations. I have attached my logo.

```html
<!DOCTYPE html>
<html lang="en">
<head>
<meta charset="utf-8">
<title>Moravel Aesthetic Doctor – Business Card</title>
<link href="https://fonts.googleapis.com/css2?family=Roboto:wght@300;400;500&display=swap" rel="stylesheet">
<style>
  :root {
    --backdrop: #dcdcdc;
    --card-white: #ffffff;
    --brand-blue: #5ec2ea;
    --text-grey: #8a8d92;
    --band-grey: #a7a9ad;
    --face-tint: #dfe9f4;
    --back-top: #a9dcf2;
    --back-mid: #aeb1b5;
    --back-bottom: #a6dbf1;
    --white: #ffffff;
  }
  * { margin: 0; padding: 0; box-sizing: border-box; }
  html, body { width: 1125px; height: 1200px; overflow: hidden; }
  body {
    background: var(--backdrop);
    font-family: 'Roboto', Arial, sans-serif;
    position: relative;
  }
  .card {
    position: absolute;
    left: 151px;
    width: 824px;
    height: 470px;
    border-radius: 24px;
    overflow: hidden;
    box-shadow: 0 3px 6px rgba(0,0,0,0.25);
  }
  /* ---------- Front ---------- */
  .card--front { top: 98px; background: var(--card-white); }
  .front__portrait {
    position: absolute; left: 255px; top: 5px; width: 570px; height: 420px;
    background: radial-gradient(ellipse at 60% 50%, var(--face-tint) 0%, rgba(223,233,244,0.5) 45%, rgba(255,255,255,0) 72%);
  }
  .brand-name {
    position: absolute; left: 50px; top: 42px;
    font-weight: 300; color: var(--text-grey); line-height: 1;
  }
  .brand-name__main { display: block; font-size: 62px; letter-spacing: 1px; }
  .brand-name__sub { display: block; font-size: 26px; letter-spacing: 1.5px; margin-top: 6px; }
  .doctor {
    position: absolute; left: 50px; top: 262px;
    font-size: 31px; font-weight: 500; color: var(--brand-blue);
  }
  .doctor__post { font-size: 19px; font-weight: 400; margin-left: 4px; }
  .qualification {
    position: absolute; left: 50px; top: 303px;
    font-size: 21px; font-weight: 300; color: var(--text-grey);
  }
  .contact {
    position: absolute; left: 50px; display: flex; align-items: center;
    font-size: 22px; font-weight: 300; color: var(--text-grey);
  }
  .contact svg { width: 20px; height: 20px; margin-right: 14px; }
  .contact--phone { top: 358px; }
  .contact--email { top: 391px; }
  .social { display: flex; align-items: center; margin-left: 30px; color: var(--brand-blue); font-size: 20px; }
  .social__dot { width: 18px; height: 18px; border-radius: 50%; background: var(--brand-blue); margin-right: 8px; }
  .front__footer { position: absolute; left: 0; bottom: 0; width: 824px; height: 40px; }
  .website {
    position: absolute; right: 40px; bottom: 8px;
    font-size: 21px; font-weight: 300; color: var(--white);
  }
  /* ---------- Back ---------- */
  .card--back {
    top: 632px;
    background: linear-gradient(180deg, var(--back-top) 0%, var(--back-mid) 42%, var(--back-mid) 62%, var(--back-bottom) 100%);
  }
  .back__portrait {
    position: absolute; left: 300px; top: 10px; width: 520px; height: 440px;
    background: radial-gradient(ellipse at 55% 50%, rgba(255,255,255,0.18) 0%, rgba(255,255,255,0) 70%);
  }
  .back__mark {
    position: absolute; left: 155px; top: 132px; width: 172px; height: 172px;
    border-radius: 50%; border: 4px solid var(--white);
  }
  .back__brand {
    position: absolute; left: 356px; top: 145px;
    font-weight: 300; color: var(--white); line-height: 1;
  }
  .back__brand .brand-name__main { font-size: 74px; }
  .back__brand .brand-name__sub { font-size: 32px; margin-top: 10px; }
  .services {
    position: absolute; left: 0; top: 326px; width: 824px;
    text-align: center; color: var(--white);
    font-size: 22px; font-weight: 300; line-height: 33px;
  }
  .services__sep { font-size: 12px; vertical-align: middle; margin: 0 6px; }
</style>
</head>
<body>

<section class="card card--front">
  <div class="front__portrait" role="img" aria-label="Faint illustration of a woman's profile with flowing hair"></div>

  <div class="brand-name">
    <span class="brand-name__main">MORAVEL</span>
    <span class="brand-name__sub">AESTHETIC DOCTOR</span>
  </div>

  <p class="doctor">Dr Elise Varden,<span class="doctor__post">MRCPCH MD</span></p>
  <p class="qualification">Australasian Diploma of Aesthetic Medicine</p>

  <p class="contact contact--phone">
    <svg viewBox="0 0 24 24" aria-hidden="true"><path fill="#5ec2ea" d="M6.6 10.8c1.4 2.8 3.8 5.1 6.6 6.6l2.2-2.2c.3-.3.7-.4 1-.2 1.1.4 2.3.6 3.6.6.6 0 1 .4 1 1V20c0 .6-.4 1-1 1C10.6 21 3 13.4 3 4c0-.6.4-1 1-1h3.5c.6 0 1 .4 1 1 0 1.3.2 2.5.6 3.6.1.3 0 .7-.2 1L6.6 10.8z"/></svg>
    0800 555 019
  </p>
  <p class="contact contact--email">
    <svg viewBox="0 0 24 24" aria-hidden="true"><rect x="2.5" y="5" width="19" height="14" rx="1.5" fill="none" stroke="#5ec2ea" stroke-width="2"/><path d="M3 6l9 7 9-7" fill="none" stroke="#5ec2ea" stroke-width="2"/></svg>
    elise@moravel.co.nz
    <span class="social"><span class="social__dot"></span>@moravel</span>
  </p>

  <svg class="front__footer" viewBox="0 0 824 40" aria-hidden="true">
    <rect x="0" y="8" width="490" height="6" fill="#5ec2ea"/>
    <path d="M490 8 L510 8 C495 8 488 16 478 22 L0 22 L0 14 L482 14 C488 11 490 8 490 8Z" fill="#ffffff"/>
    <path d="M510 0 L824 0 L824 40 L0 40 L0 26 L472 26 C490 26 492 0 510 0Z" fill="#a7a9ad"/>
  </svg>
  <p class="website">www.moravel.co.nz</p>
</section>

<section class="card card--back">
  <div class="back__portrait" role="img" aria-label="Faint illustration of a woman's profile"></div>
  <div class="back__mark"></div>
  <div class="brand-name back__brand">
    <span class="brand-name__main">MORAVEL</span>
    <span class="brand-name__sub">AESTHETIC DOCTOR</span>
  </div>
  <div class="services">
    <p>Dermal injectables<span class="services__sep">●</span>Plasma facials<span class="services__sep">●</span>Microneedling</p>
    <p>Skin boosters<span class="services__sep">●</span>Excessive sweating</p>
    <p>Home and Spa Based Treatments</p>
  </div>
</section>

</body>
</html>
```